Automotive eCommerce Business looking for a business card design

Looking for a clean and simple business card design. Our company name is "Brindle Auto" and we are a company specializing in the ecommerce sales of automotive parts, specifically for pick up trucks and large SUVs. Our company colours are red, black, and white.

Feel free to use the logo provided or create a new logo that you seem fit. Looking forward to your creative ideas!

Industry/Entity Type

Automotive

Contact Information for Business Card

We were thinking of a possibly two-sided design featuring just the logo and company name on one side, and personal information on the other side. Single sided designs will be considered as well.

Font styles to use
Serif
Sans Serif
Decorative

Colors
ec1f27
ffffff
000000

Requirements
Must have
• Space for employee's name, title, phone number and email address, along with the company address and website somewhere.

```html
<!DOCTYPE html>
<html lang="en">
<head>
<meta charset="utf-8">
<title>Brindle Auto – Business Card</title>
<link href="https://fonts.googleapis.com/css2?family=Source+Sans+3:wght@400;600&display=swap" rel="stylesheet">
<style>
  :root {
    --stage: #000000;
    --brand-red: #a51f23;
    --paper: #ffffff;
    --ink: #1a1a1a;
    --divider: rgba(255,255,255,0.18);
  }
  * { margin: 0; padding: 0; box-sizing: border-box; }
  html, body {
    width: 1200px; height: 900px; overflow: hidden;
    background: var(--stage);
    font-family: "Source Sans 3", "Myriad Pro", Arial, sans-serif;
  }
  .stage { position: relative; width: 1200px; height: 900px; }
  .card {
    position: absolute; top: 271px;
    width: 457px; height: 281px;
    border-radius: 14px; overflow: hidden;
  }
  .card--contact { left: 137px; background: var(--brand-red); color: var(--paper); }
  .card--brand { left: 626px; background: var(--paper); }

  .contact-brand {
    position: absolute; left: 40px; top: 112px; width: 160px;
    text-align: center; font-size: 22px; font-weight: 600; color: var(--paper);
    letter-spacing: 0.5px;
  }
  .contact-brand .brand-square {
    display: block; width: 34px; height: 34px; margin: 0 auto 10px;
    background: var(--paper);
  }
  .divider {
    position: absolute; left: 204px; top: 67px;
    width: 1px; height: 141px; background: var(--divider);
  }
  .details { position: absolute; left: 250px; top: 64px; }
  .person-name { font-size: 19px; font-weight: 400; line-height: 22px; }
  .person-title { font-size: 13px; line-height: 16px; }
  .address { margin-top: 11px; font-size: 13px; line-height: 17px; }
  .contact-list { list-style: none; margin-top: 10px; font-size: 13px; line-height: 16.5px; }
  .contact-list li { display: flex; align-items: center; gap: 7px; }
  .contact-list svg { width: 9px; height: 9px; fill: var(--paper); flex: none; }

  .brand-lockup {
    position: absolute; left: 0; right: 0; top: 62px; text-align: center;
  }
  .brand-lockup .brand-square {
    display: block; width: 100px; height: 100px; margin: 0 auto 32px;
    background: var(--brand-red); border-radius: 8px;
  }
  .brand-name {
    font-size: 32px; font-weight: 400; color: var(--ink); letter-spacing: 2px;
  }
</style>
</head>
<body>
<main class="stage">
  <section class="card card--contact">
    <div class="contact-brand"><span class="brand-square"></span>Brindle Auto</div>
    <div class="divider"></div>
    <div class="details">
      <p class="person-name">Marcus Hale</p>
      <p class="person-title">Managing Director</p>
      <p class="address">48 Foundry Lane<br>Northvale, 204519.</p>
      <ul class="contact-list">
        <li><svg viewBox="0 0 10 10"><path d="M2 0.5 3.6 2.6 2.8 3.6C3.4 5 5 6.6 6.4 7.2L7.4 6.4 9.5 8 8.6 9.4C4.5 9.4 0.6 5.5 0.6 1.4Z"/></svg>044-987 654 321</li>
        <li><svg viewBox="0 0 10 10"><path d="M0.5 2h9v6h-9Z M1 2.5 5 5.5 9 2.5" fill="none" stroke="#fff" stroke-width="1"/></svg>hello@brindleauto.com</li>
        <li><svg viewBox="0 0 10 10"><path d="M4 6 6 4M3.5 5 2 6.5a1.4 1.4 0 0 0 1.5 1.5L5 6.5M6.5 5 8 3.5A1.4 1.4 0 0 0 6.5 2L5 3.5" fill="none" stroke="#fff" stroke-width="1.2" stroke-linecap="round"/></svg>www.brindleauto.com</li>
      </ul>
    </div>
  </section>

  <section class="card card--brand">
    <div class="brand-lockup">
      <span class="brand-square"></span>
      <p class="brand-name">Brindle Auto Ltd</p>
    </div>
  </section>
</main>
</body>
</html>
```